Harborline Renewal Business Card Design

Professional and clean design. The design colors should flow with the logo. Two-sided card with the website on the back which is:

www.HarborlineRenewal.example.

"Specializing in Water Damage Restoration"

On the front I need the name, email, phone, and logo.

Name: Darnell Quisby
Email: Darnell@HarborlineRenewal.example
Phone: 555-318-2046 for now

I only have the Preview and Thumbnail right now but should have the source files uploaded within a day or two.

Target Market(s)

Flood victims, home owners with water damage from busted pipes etc...

Industry/Entity Type

Business

Contact Information for Business Card

Name: Darnell Quisby

Font styles to use
Serif
Sans Serif

Requirements
Must have
• Business Card Details Info

```html
<!DOCTYPE html>
<html lang="en">
<head>
<meta charset="UTF-8">
<title>Harborline Renewal Business Card</title>
<link rel="stylesheet" href="https://fonts.googleapis.com/css2?family=Arimo:wght@400;700&display=swap">
<style>
  :root {
    --stage: #e8e5e0;
    --card-dark: #0b0b0c;
    --card-light: #ffffff;
    --brand-blue: #2f9fd9;
    --circle-fill: #5cc1ee;
    --circle-ring: #2b98d3;
    --ink-light: #ffffff;
  }
  html, body {
    margin: 0;
    padding: 0;
    width: 1200px;
    height: 950px;
    overflow: hidden;
    background: var(--stage);
    font-family: "Arimo", Arial, sans-serif;
  }
  .stage {
    position: relative;
    width: 1200px;
    height: 950px;
  }
  .card {
    position: absolute;
    left: 270px;
    width: 660px;
    height: 377px;
    overflow: hidden;
    box-shadow: 0 10px 28px rgba(0,0,0,0.25);
  }
  .card--back {
    top: 70px;
    background: var(--card-dark);
  }
  .card--front {
    top: 500px;
    background: var(--card-light);
  }
  .brand {
    display: flex;
    align-items: center;
    gap: 12px;
    color: var(--brand-blue);
    font-weight: 700;
    font-size: 30px;
    letter-spacing: 0.04em;
    text-transform: uppercase;
  }
  .brand__dot {
    width: 38px;
    height: 38px;
    border-radius: 50%;
    background: var(--brand-blue);
    flex: none;
  }
  .card--back .brand {
    position: absolute;
    left: 0;
    right: 0;
    top: 128px;
    justify-content: center;
  }
  .tagline {
    position: absolute;
    left: 0;
    right: 0;
    top: 208px;
    text-align: center;
    color: var(--ink-light);
    font-size: 17px;
    letter-spacing: 0.02em;
  }
  .card--front .brand {
    position: absolute;
    left: 62px;
    top: 62px;
    font-size: 26px;
  }
  .card--front .brand__dot {
    width: 32px;
    height: 32px;
  }
  .contact-circle {
    position: absolute;
    left: 245px;
    top: 110px;
    width: 470px;
    height: 470px;
    border-radius: 50%;
    background: var(--circle-fill);
    box-shadow: 0 0 0 4px var(--card-light), 0 0 0 7px var(--circle-ring);
  }
  .contact {
    position: absolute;
    right: 40px;
    top: 190px;
    text-align: right;
    color: var(--ink-light);
  }
  .contact__name {
    font-size: 25px;
    font-weight: 700;
    margin: 0 0 10px;
  }
  .contact__line {
    display: flex;
    justify-content: flex-end;
    align-items: center;
    gap: 8px;
    font-size: 17px;
    line-height: 26px;
    margin: 0;
  }
  .contact__icon {
    width: 16px;
    height: 16px;
    flex: none;
  }
</style>
</head>
<body>
<main class="stage">
  <section class="card card--back" aria-label="Card back">
    <div class="brand"><span class="brand__dot"></span>Harborline Renewal</div>
    <p class="tagline">Specializing in Water Damage Restoration</p>
  </section>

  <section class="card card--front" aria-label="Card front">
    <div class="brand"><span class="brand__dot"></span>Harborline Renewal</div>
    <div class="contact-circle"></div>
    <div class="contact">
      <p class="contact__name">Darnell Quisby</p>
      <p class="contact__line">555-318-2046 for now
        <svg class="contact__icon" viewBox="0 0 16 16" aria-hidden="true"><path fill="#fff" d="M3.5 1.5l2.5 0 1 3.5-1.6 1.2a8 8 0 0 0 4.4 4.4L11 9l3.5 1v2.5c0 1-1 2-2 2A11 11 0 0 1 1.5 3.5c0-1 1-2 2-2z"/></svg>
      </p>
      <p class="contact__line">Darnell@HarborlineRenewal.example
        <svg class="contact__icon" viewBox="0 0 16 16" aria-hidden="true"><rect x="1" y="3" width="14" height="10" rx="1" fill="#fff"/><path d="M1.5 3.8L8 9l6.5-5.2" fill="none" stroke="#5cc1ee" stroke-width="1.3"/></svg>
      </p>
      <p class="contact__line">HarborlineRenewal.example
        <svg class="contact__icon" viewBox="0 0 16 16" aria-hidden="true"><circle cx="8" cy="8" r="7" fill="#fff"/><circle cx="8" cy="6" r="2" fill="#5cc1ee"/><rect x="6.5" y="9" width="3" height="4" fill="#5cc1ee"/></svg>
      </p>
    </div>
  </section>
</main>
</body>
</html>
```